Tolvar Air and Electrical Website

Simple and easy to use website for a Electrical and Air Conditioning contracting business.Use stock photosOnline contact portallogo still to be supplied

Target Market(s)

Mums and Dads who want a local contractor

Coding

Coded - Design and coding required

Number of Pages Required

2 page

Font styles to use
Sans Serif

Colors
f04a50
3276b5
33a6d7

Requirements
Must have
• Simple and easy to use
• Ph number
• 4 web address; linked to page
• 0417385926
• tolvar.com.au
• tolvarelectrical.com.au
• tolvarairandelectrical.com.au
• tolvarair.com.au
Nice to have
• Split System Air Con Picture
• Electrical Pictures

```html
<!DOCTYPE html>
<html lang="en">
<head>
<meta charset="utf-8">
<title>Tolvar Air and Electrical</title>
<link href="https://fonts.googleapis.com/css2?family=Open+Sans:ital,wght@0,400;0,600;0,700;1,400&family=Montserrat:wght@600;700&display=swap" rel="stylesheet">
<style>
:root{
  --red:#f04a50;
  --blue:#3276b5;
  --sky:#33a6d7;
  --ink:#333;
  --muted:#777;
  --line:#ddd;
  --grey-row:#e2e2e2;
  --num:#5b7fa6;
  --dark:#2b2b2b;
}
*{margin:0;padding:0;box-sizing:border-box}
html,body{width:1200px;height:4580px;overflow:hidden;background:#fff}
body{font-family:"Open Sans",Arial,sans-serif;color:var(--ink);position:relative}
.abs{position:absolute}
.btn{position:absolute;display:flex;align-items:center;justify-content:center;background:var(--sky);color:#fff;font-size:12px;font-weight:600;letter-spacing:.5px;border-radius:20px;text-transform:uppercase}
.section-title{position:absolute;left:0;width:1200px;text-align:center;color:var(--red);font-size:34px;font-weight:600;text-transform:uppercase}

/* header */
.site-header{position:absolute;top:0;left:0;width:1200px;height:110px;background:#fff}
.brand{position:absolute;left:80px;top:30px;display:flex;align-items:center;gap:12px}
.brand-square{width:30px;height:30px;background:var(--red)}
.brand-name{font-size:24px;font-weight:700;color:var(--blue);line-height:1.05}
.brand-name small{display:block;font-size:11px;letter-spacing:2px;font-weight:700;color:var(--blue)}
.call-us{position:absolute;left:800px;top:22px;color:var(--red);font-size:18px}
.appointment{left:1030px;top:20px;width:180px;height:30px;font-size:11px}
.main-nav{position:absolute;left:420px;top:74px;display:flex;gap:38px;font-size:13px;color:#555}
.main-nav .current{color:var(--red)}

/* hero */
.hero{position:absolute;top:110px;left:0;width:1200px;height:546px;overflow:hidden}
.hero-photo{position:absolute;inset:0;background:linear-gradient(100deg,#7d8a96 0%,#a9b3bb 45%,#c8cdd0 70%,#9aa3a8 100%)}
.hero-curve{position:absolute;left:0;bottom:0}
.hero h1{position:absolute;left:80px;top:120px;font-family:Montserrat,sans-serif;color:#fff;font-size:42px;font-weight:700;line-height:1.15;letter-spacing:1px}
.hero .tagline{position:absolute;left:80px;top:225px;color:#fff;font-size:25px;font-weight:600}
.hero .btn{left:80px;top:290px;width:120px;height:34px}
.hero-dots{position:absolute;left:565px;top:462px;display:flex;gap:10px}
.hero-dots i{width:11px;height:11px;border-radius:50%;border:2px solid #fff;display:block}
.hero-dots i:first-child{background:#fff}

/* about */
.about-sub{position:absolute;left:0;width:1200px;text-align:center}
.about-lead{top:785px;font-size:26px;color:#333}
.about-lead2{top:826px;font-size:16px;color:#555}
.about-text{top:858px;font-size:12px;line-height:19px;color:#777;left:360px;width:480px}
.read-more{position:absolute;left:520px;top:927px;width:160px;text-align:center;font-size:11px;color:var(--blue);border-bottom:1px solid #999;padding-bottom:8px;letter-spacing:1px}

/* feature tiles */
.tiles{position:absolute;top:1038px;left:0;width:1200px;height:238px;display:flex;gap:4px}
.tile{flex:1;position:relative;color:#fff;text-align:center}
.tile-photo{position:absolute;inset:0}
.tile-1 .tile-photo{background:linear-gradient(135deg,#3d4650,#8d98a2)}
.tile-2 .tile-photo{background:linear-gradient(135deg,#b7bec4,#8a9097)}
.tile-3 .tile-photo{background:linear-gradient(135deg,#5a6a78,#b0b9c0)}
.tile-body{position:absolute;left:0;right:0;top:100px}
.tile h3{font-size:28px;font-weight:600}
.tile p{font-size:12px;margin:6px auto 0;width:260px;line-height:17px}
.tile .btn{position:relative;margin:12px auto 0;width:100px;height:28px;font-size:10px}

/* services */
.slider-arrow{position:absolute;width:26px;height:26px;border-radius:50%;border:1px solid #333;display:flex;align-items:center;justify-content:center}
.service-card{position:absolute;top:1420px;width:445px}
.service-photo{height:280px}
.service-list{margin:30px 0 0 28px;border-left:4px solid var(--red);padding-left:12px}
.service-list h4{font-size:14px;font-weight:700;letter-spacing:1px;margin-left:-16px;padding-left:12px}
.service-list ul{list-style:none;margin-top:8px}
.service-list li{font-size:11px;color:#555;line-height:20px}
.service-list li::before{content:"›";color:var(--red);margin-right:8px}

/* breakdown band */
.band{position:absolute;top:2091px;left:0;width:1200px;height:284px;background:var(--sky);color:#fff;text-align:center}
.band h2{margin-top:58px;font-size:22px;font-weight:700}
.band p{width:520px;margin:12px auto 0;font-size:13px;line-height:22px}
.band .btn{position:relative;margin:16px auto 0;width:130px;height:30px;background:transparent;border:1px solid #fff}

/* testimonial */
.testimonial{position:absolute;left:85px;top:2519px;width:1025px;height:336px;border:2px solid #bbb;text-align:center}
.testimonial h3{margin-top:80px;color:var(--sky);font-size:19px;font-weight:400}
.testimonial blockquote{font-style:italic;color:#666;font-size:14px;line-height:22px;margin-top:12px}
.avatar{width:52px;height:52px;border-radius:50%;background:linear-gradient(#8ba8c4,#44688e);margin:14px auto 0}
.reviewer{font-size:13px;font-weight:600;margin-top:8px;letter-spacing:.5px}
.review-date{font-size:11px;color:#777}
.stars{color:var(--red);font-size:13px;letter-spacing:2px}

/* categories */
.cat{position:absolute;width:290px;display:flex;gap:16px}
.cat svg{flex:none;margin-top:4px}
.cat h4{font-size:15px;font-weight:600}
.cat p{font-size:12px;color:#666;line-height:16px;margin-top:4px}
.cat .more{font-size:11px;font-weight:600;margin-top:6px}
.cat-active{border:2px solid var(--sky);padding:14px 16px;box-shadow:0 2px 10px rgba(0,0,0,.12)}
.cat-active .more{color:var(--sky)}

/* suburbs */
.suburbs-title{position:absolute;left:80px;top:3430px;color:var(--red);font-size:32px;font-weight:600}
.suburbs-intro{position:absolute;left:80px;top:3484px;width:500px;font-size:13px;color:#777;line-height:22px}
.suburb-list{position:absolute;left:80px;top:3562px;width:400px;list-style:none}
.suburb-list li{display:flex;height:64px;margin-bottom:18px;background:var(--grey-row);align-items:center;font-size:13px}
.suburb-list b{width:64px;height:64px;background:var(--num);color:#fff;display:flex;align-items:center;justify-content:center;font-weight:600;margin-right:26px}
.suburbs-art{position:absolute;left:640px;top:3430px;width:430px;height:560px;border-radius:210px 210px 60px 60px;background:linear-gradient(#cfe3f2,#f6d77a)}

/* footer */
.site-footer{position:absolute;top:4121px;left:0;width:1200px;height:459px;background:linear-gradient(120deg,#2f2f2f,#4a4a4a 60%,#3a3a3a);color:#ddd}
.contact-block{position:absolute;left:80px;top:110px}
.call-line{display:flex;align-items:center;gap:12px;color:var(--sky);font-size:30px}
.email{font-size:13px;margin-left:46px}
.hours{margin:18px 0 0 46px;font-size:12px;line-height:18px;display:flex;gap:40px}
.hours strong{display:block;font-weight:600}
.address{margin:16px 0 0 46px;font-size:12px;line-height:18px;position:relative}
.social{position:absolute;left:116px;top:330px;display:flex;gap:12px}
.social i{width:28px;height:28px;border-radius:50%;background:#666;display:block}
.social i:nth-child(2){background:var(--sky)}
.legal{position:absolute;left:80px;top:415px;font-size:11px;color:#aaa;display:flex;gap:40px}
.quote-form{position:absolute;left:720px;top:30px;width:360px;height:355px;background:#111;padding:20px 32px}
.quote-form h3{color:#fff;text-align:center;font-size:20px;font-weight:600}
.field{background:#fff;height:34px;margin-top:14px;font-size:11px;color:#666;padding:9px 12px}
.field.msg{height:100px}
.quote-form .btn{position:relative;margin-top:14px;width:100%;height:34px;border-radius:0}
</style>
</head>
<body>

<header class="site-header">
  <div class="brand"><span class="brand-square"></span><span class="brand-name">TOLVAR<small>AIR AND ELECTRICAL</small></span></div>
  <div class="call-us">Call Us: 0417385926</div>
  <div class="btn appointment">Make an Appointment</div>
  <nav class="main-nav">
    <span class="current">Home</span><span>About Us</span><span>Services</span><span>Service Categories</span><span>Why Choose ▾</span><span>Testimonials</span><span>Contact Us</span>
  </nav>
</header>

<section class="hero">
  <div class="hero-photo" role="img" aria-label="Technician servicing an outdoor split system air conditioning unit"></div>
  <h1>IF IT IS ELECTRONICAL,<br>WE DO IT</h1>
  <div class="tagline">Serving The Electronical Needs</div>
  <div class="btn">Contact Us</div>
  <div class="hero-dots"><i></i><i></i><i></i><i></i></div>
  <svg class="hero-curve" width="1200" height="90" viewBox="0 0 1200 90"><path d="M0 20 Q600 110 1200 20 L1200 90 L0 90 Z" fill="#fff"/><path d="M596 58 L590 76 L598 74 L592 90 L606 68 L598 70 L604 58 Z" fill="var(--sky)"/></svg>
</section>

<section class="about">
  <h2 class="section-title" style="top:735px">About Us</h2>
  <p class="about-sub about-lead">With over 17 years' experience in the Electrical Industry</p>
  <p class="about-sub about-lead2">Tolvar Electrical provides a superior level of knowledge</p>
  <p class="about-sub about-text">To provide our customers with an immediate response and on time quality work, and deliver on time, every time. Our friendly tradesmen are always professional, attired and treat your home or business with respect - we leave our jobs clean and tidy.</p>
  <div class="read-more">READ MORE &nbsp;→</div>
</section>

<section class="tiles">
  <div class="tile tile-1"><div class="tile-photo" role="img" aria-label="Electrician working on a switchboard"></div><div class="tile-body"><h3>Why Us</h3><p>We are a local team you can call on any day of the week.</p></div></div>
  <div class="tile tile-2"><div class="tile-photo" role="img" aria-label="Hands fitting electrical wiring"></div><div class="tile-body" style="top:70px"><h3>Quality</h3><p>We are committed to safe and reliable electrical work done right.</p><div class="btn">Read More</div></div></div>
  <div class="tile tile-3"><div class="tile-photo" role="img" aria-label="Customer reviewing a quote on a laptop"></div><div class="tile-body"><h3>Price</h3><p>Price is always upfront, fair and clear with no hidden extras.</p></div></div>
</section>

<section class="services">
  <h2 class="section-title" style="top:1350px">Services</h2>
  <div class="slider-arrow" style="left:26px;top:1546px"><svg width="10" height="10"><path d="M7 1 L2 5 L7 9" stroke="#333" stroke-width="2" fill="none"/></svg></div>
  <div class="slider-arrow" style="left:1144px;top:1546px"><svg width="10" height="10"><path d="M3 1 L8 5 L3 9" stroke="#333" stroke-width="2" fill="none"/></svg></div>
  <div class="service-card" style="left:120px">
    <div class="service-photo" role="img" aria-label="Electrician testing a domestic switchboard" style="background:linear-gradient(135deg,#6d7882,#c9ccd0 55%,#b34a3e)"></div>
    <div class="service-list"><h4>DOMESTIC</h4><ul><li>Watts</li><li>Switchboards</li><li>Lighting Installation</li><li>LED lighting</li><li>Fans and ventilation</li><li>General Electrical wiring installations</li><li>Safety Switches</li><li>Power points</li></ul></div>
  </div>
  <div class="service-card" style="left:625px">
    <div class="service-photo" role="img" aria-label="Technician on a ladder installing a commercial air conditioner" style="background:linear-gradient(135deg,#8e9aa5,#d6d9dc 60%,#c96b3d)"></div>
    <div class="service-list"><h4>COMMERCIAL</h4><ul><li>Complete Office Fit Outs</li><li>Complete Retail &amp; Restaurant Fit Outs</li><li>Energy Efficient Lighting</li><li>Commercial Safety Switches</li><li>Audio Visual Installations</li><li>Emergency &amp; Exit Lighting</li><li>Retail Lighting Upgrades</li></ul></div>
  </div>
  <div class="btn" style="left:530px;top:1978px;width:140px;height:30px">View All Services</div>
</section>

<section class="band">
  <h2>24hr Breakdown &amp; Repair Service</h2>
  <p>Tolvar Electrical has a qualified electrician standing by with a fully stocked truck to assist you and your electrical needs around the clock. 24 hour emergency electrical services for your convenience.</p>
  <div class="btn">Contact Us</div>
</section>

<section>
  <div class="testimonial">
    <h3>Split System Air ConditioningVerifiedHired</h3>
    <blockquote>"Dale was very prompt and responsive. His team were very professional and friendly guys.<br>Thanks for the great job! ..."</blockquote>
    <div class="avatar" role="img" aria-label="Reviewer avatar"></div>
    <div class="reviewer">KYLIE FROM PRESTON, VIC</div>
    <div class="review-date">6 MAY 2019</div>
    <div class="stars">★★★★★</div>
  </div>
  <svg class="abs" style="left:545px;top:2460px" width="110" height="110" viewBox="0 0 110 110"><rect x="22" y="22" width="66" height="66" transform="rotate(45 55 55)" fill="var(--dark)"/><text x="55" y="66" text-anchor="middle" fill="#fff" font-family="Open Sans,sans-serif" font-size="30" font-weight="700">66</text></svg>
  <svg class="abs" style="left:74px;top:2667px" width="24" height="24"><circle cx="12" cy="12" r="11" fill="#333"/><path d="M14 7 L9 12 L14 17" stroke="#fff" stroke-width="2" fill="none"/></svg>
  <svg class="abs" style="left:1098px;top:2667px" width="24" height="24"><circle cx="12" cy="12" r="11" fill="var(--sky)"/><path d="M10 7 L15 12 L10 17" stroke="#fff" stroke-width="2" fill="none"/></svg>
  <div class="btn" style="left:545px;top:2872px;width:110px;height:28px">View All</div>
</section>

<section class="categories">
  <h2 class="section-title" style="top:2968px">Service Categories</h2>
  <div class="cat" style="left:120px;top:3038px"><svg width="34" height="24"><rect x="2" y="4" width="30" height="12" rx="2" fill="none" stroke="#333" stroke-width="2"/><path d="M8 20h18" stroke="#333" stroke-width="2"/></svg><div><h4>Air Conditioning</h4><p>Lorem ipsum dolor sit amet, consectetur...</p><div class="more">Read More ›</div></div></div>
  <div class="cat" style="left:480px;top:3038px"><svg width="34" height="30"><rect x="4" y="2" width="20" height="26" fill="none" stroke="#333" stroke-width="2"/><path d="M9 9h10M9 15h10M9 21h6" stroke="#333" stroke-width="2"/></svg><div><h4>Installation</h4><p>Lorem ipsum dolor sit amet, consectetur...</p><div class="more">Read More ›</div></div></div>
  <div class="cat" style="left:840px;top:3038px"><svg width="34" height="30"><circle cx="12" cy="14" r="8" fill="none" stroke="#333" stroke-width="2"/><path d="M18 20l10 8" stroke="#333" stroke-width="3"/></svg><div><h4>Repairs &amp; Maintenance</h4><p>Lorem ipsum dolor sit amet, consectetur...</p><div class="more">Read More ›</div></div></div>
  <div class="cat" style="left:120px;top:3160px"><svg width="34" height="30"><path d="M17 3a8 8 0 0 0-5 14v4h10v-4a8 8 0 0 0-5-14z" fill="none" stroke="#333" stroke-width="2"/><path d="M13 25h8" stroke="#333" stroke-width="2"/></svg><div><h4>Lighting</h4><p>Lorem ipsum dolor sit amet, consectetur...</p><div class="more">Read More ›</div></div></div>
  <div class="cat cat-active" style="left:480px;top:3140px;width:280px"><svg width="40" height="40"><circle cx="20" cy="20" r="19" fill="var(--sky)"/><circle cx="20" cy="20" r="9" fill="none" stroke="#fff" stroke-width="2"/><path d="M20 14v6l4 3" stroke="#fff" stroke-width="2" fill="none"/></svg><div><h4>24/7 Emergency Electricians</h4><p>Lorem ipsum dolor sit amet, consectetur...</p><div class="more">Read More ›</div></div></div>
  <div class="cat" style="left:840px;top:3160px"><svg width="34" height="30"><path d="M4 15L17 4l13 11M8 12v14h18V12" fill="none" stroke="#333" stroke-width="2"/></svg><div><h4>Repairs &amp; Maintenance</h4><p>Lorem ipsum dolor sit amet, consectetur...</p><div class="more">Read More ›</div></div></div>
  <div class="btn" style="left:545px;top:3304px;width:110px;height:28px">View All</div>
</section>

<section class="suburbs">
  <h2 class="suburbs-title">SUBURBS SERVICED</h2>
  <p class="suburbs-intro">Lorem ipsum dolor sit amet, consectetur adipiscing elit, sed do eiusmod tempor incididunt ut labore et dolore magna aliqua.</p>
  <ol class="suburb-list">
    <li><b>1</b>Air Conditioning in Bentleigh East</li>
    <li><b>2</b>Electricians in Bentleigh East</li>
    <li><b>3</b>Air Conditioning in Brighton</li>
    <li><b>4</b>Electricians in Brighton</li>
    <li><b>5</b>Air Conditioning in Eltham</li>
    <li><b>6</b>Electricians in Eltham</li>
  </ol>
  <div class="suburbs-art" role="img" aria-label="Illustration of a technician installing an air conditioner inside a light bulb outline"></div>
  <div class="btn" style="left:545px;top:4046px;width:110px;height:28px">View All</div>
</section>

<footer class="site-footer" role="contentinfo">
  <div class="contact-block">
    <div class="call-line"><svg width="34" height="34"><circle cx="17" cy="17" r="16" fill="none" stroke="#fff" stroke-width="2"/><path d="M11 10c0 8 5 13 13 14l2-3-4-2-2 2c-3-1-5-3-6-6l2-2-2-4z" fill="#fff"/></svg>Call. (041)738.5926</div>
    <div class="email">e. contact@tolvar.com.au</div>
    <div class="hours"><div><strong>Operating Hours</strong>Monday to Friday<br>7am - 7pm</div><div><strong>&nbsp;</strong>For Saturday<br>7am - 6pm</div></div>
    <div class="address">Dale Morton<br>Oakleigh VIC 3166</div>
  </div>
  <svg class="abs" style="left:84px;top:218px" width="14" height="18"><path d="M7 1a6 6 0 0 0-6 6c0 5 6 10 6 10s6-5 6-10a6 6 0 0 0-6-6z" fill="#fff"/></svg>
  <svg class="abs" style="left:84px;top:290px" width="14" height="18"><path d="M7 1a6 6 0 0 0-6 6c0 5 6 10 6 10s6-5 6-10a6 6 0 0 0-6-6z" fill="#fff"/></svg>
  <div class="social"><i></i><i></i><i></i></div>
  <div class="legal"><span>© 2019 Tolvar. All Rights Reserved</span><span>Terms and Conditions</span><span>Privacy policy</span></div>
  <form class="quote-form">
    <h3>Get a free Quote</h3>
    <div class="field">Name*</div>
    <div class="field">Email*</div>
    <div class="field">Phone Number*</div>
    <div class="field msg">Message*</div>
    <div class="btn">Send</div>
  </form>
</footer>

</body>
</html>
```